Keystone ridge construction brochure

i would like a brochure that can be send to clients digitally and printed. we are a geotechnical, foundation, and concrete company. I attached info below

Target Market(s)

Construction managers, general contractors, developers, municipalities, private, and commercial partners.

Industry/Entity Type

Geotechnical / foundation

Font styles to use
Serif
Other font styles liked:
• Maybe same as logo

Colors
0054AA
0677BA
7BADD7
CADEEF
E8F1F8

```html
<!DOCTYPE html>
<html lang="en">
<head>
<meta charset="utf-8">
<title>Keystone Ridge Construction Brochure</title>
<link href="https://fonts.googleapis.com/css2?family=Montserrat:wght@300;400;600;700;800&family=Hind:wght@300;400&display=swap" rel="stylesheet">
<style>
  :root {
    --navy: #0b2450;
    --hero-dark: #050b1a;
    --hero-blue: #06244f;
    --panel: #f2f2f2;
    --heading-grey: #5c5c5c;
    --body-grey: #6a6a6a;
    --white: #ffffff;
    --earth-1: #8a6b4e;
    --earth-2: #5a4636;
    --earth-3: #c9a47c;
  }
  * { margin: 0; padding: 0; box-sizing: border-box; }
  html, body { width: 848px; height: 1200px; overflow: hidden; background: var(--white); }
  .brochure { position: relative; width: 848px; height: 1200px; overflow: hidden; font-family: "Hind", sans-serif; color: var(--body-grey); }

  /* Hero */
  .hero { position: absolute; left: 0; top: 0; width: 848px; height: 522px; overflow: hidden; }
  .hero-photo { position: absolute; inset: 0; background: radial-gradient(ellipse at 75% 30%, var(--earth-1) 0%, var(--earth-2) 45%, #2d241d 80%), var(--earth-2); }
  .hero-photo::after { content: ""; position: absolute; inset: 0; background: linear-gradient(160deg, transparent 55%, var(--earth-3) 100%); opacity: .7; }
  .hero-shapes { position: absolute; inset: 0; }
  .brand-name { position: absolute; left: 32px; top: 44px; font-family: "Montserrat", sans-serif; font-weight: 800; font-size: 38px; line-height: 42px; letter-spacing: 1px; color: var(--white); }
  .hero-title { position: absolute; left: 32px; top: 208px; font-family: "Montserrat", sans-serif; font-weight: 700; font-size: 38px; line-height: 44px; color: var(--white); }
  .hero-title .light { display: block; margin-top: 10px; font-weight: 400; }
  .hero-tagline { position: absolute; left: 34px; top: 414px; font-family: "Montserrat", sans-serif; font-weight: 400; font-size: 21px; color: var(--white); letter-spacing: .3px; }

  /* Left panel */
  .info-panel { position: absolute; left: 4px; top: 529px; width: 463px; height: 649px; background: var(--panel); }
  .footer-bar { position: absolute; left: 0; top: 1178px; width: 467px; height: 22px; background: var(--navy); }
  .section-heading { position: absolute; font-family: "Montserrat", sans-serif; font-weight: 700; font-size: 22px; line-height: 29px; color: var(--heading-grey); }
  .rule { position: absolute; width: 91px; height: 2px; background: var(--navy); }
  .body-text { position: absolute; font-size: 14px; line-height: 20.5px; font-weight: 300; text-align: justify; color: var(--body-grey); }

  .reasons { position: absolute; left: 36px; top: 850px; width: 320px; display: grid; grid-template-columns: 171px 150px; row-gap: 10px; list-style: none; }
  .reasons li { position: relative; padding-left: 13px; font-size: 14px; line-height: 17px; font-weight: 300; color: var(--body-grey); }
  .reasons li::before { content: ""; position: absolute; left: 0; top: 5px; width: 6px; height: 6px; border-radius: 50%; background: var(--navy); }

  /* Services */
  .services-frame { position: absolute; left: 589px; top: 547px; width: 233px; height: 481px; background: var(--navy); }
  .services-card { position: absolute; left: 375px; top: 571px; width: 428px; height: 433px; background: var(--white); }
  .service { position: absolute; left: 405px; width: 360px; }
  .service-icon { position: absolute; left: 0; top: 0; width: 47px; height: 47px; }
  .service-title { position: absolute; left: 63px; top: -7px; font-family: "Montserrat", sans-serif; font-weight: 600; font-size: 13.5px; letter-spacing: -.2px; color: var(--navy); white-space: nowrap; }
  .service-text { position: absolute; left: 63px; top: 14px; width: 297px; font-size: 14px; line-height: 20.5px; font-weight: 300; text-align: justify; color: var(--body-grey); }

  /* Contact */
  .call-label { position: absolute; left: 505px; top: 1060px; font-family: "Montserrat", sans-serif; font-weight: 700; font-size: 20px; color: var(--heading-grey); }
  .call-number { position: absolute; left: 505px; top: 1085px; font-family: "Montserrat", sans-serif; font-weight: 400; font-size: 28px; color: var(--navy); }
  .contact-line { position: absolute; left: 510px; top: 1131px; width: 1.5px; height: 42px; background: var(--heading-grey); }
  .contact-list { position: absolute; left: 525px; top: 1129px; display: grid; grid-template-columns: 81px auto; row-gap: 3px; font-family: "Montserrat", sans-serif; font-size: 9px; line-height: 13px; }
  .contact-list dt { font-weight: 700; color: var(--navy); }
  .contact-list dd { font-weight: 400; color: var(--heading-grey); }
</style>
</head>
<body>
<main class="brochure">

  <section class="hero">
    <div class="hero-photo" role="img" aria-label="Close-up photo of a helical auger drilling into sandy soil on a foundation site"></div>
    <svg class="hero-shapes" width="848" height="522" viewBox="0 0 848 522" aria-hidden="true">
      <polygon points="0,0 298,0 669,522 0,522" fill="var(--hero-dark)" opacity="0.93"/>
      <polygon points="298,0 413,0 358,81" fill="var(--hero-blue)"/>
    </svg>
    <div class="brand-name">KEYSTONE<br>RIDGE</div>
    <h1 class="hero-title">BUILDING STRONG<br>FOUNDATIONS.<span class="light">DELIVERING LASTING<br>RESULTS.</span></h1>
    <p class="hero-tagline">Geotechnical · Foundation · Concrete Specialists</p>
  </section>

  <div class="info-panel"></div>
  <div class="footer-bar"></div>

  <h2 class="section-heading" style="left:32px; top:553px;">ABOUT KEYSTONE RIDGE<br>CONSTRUCTION</h2>
  <div class="rule" style="left:32px; top:616px;"></div>
  <p class="body-text" style="left:31px; top:636px; width:311px;">Lorem ipsum dolor sit amet, consectetur adipiscing elit, sed do eiusmod tempor incididunt ut labore et dolore magna aliqua. Quis ipsum suspendisse ultrices gravida. Risus commodo viverra maecenas accumsan lacus vel facilisis.</p>

  <h2 class="section-heading" style="left:32px; top:765px;">WHY CHOOSE KEYSTONE<br>RIDGE?</h2>
  <div class="rule" style="left:32px; top:828px;"></div>
  <ul class="reasons">
    <li>Proven Industry Experience</li>
    <li>Expert Geotechnical Solutions</li>
    <li>Specialized Foundation Construction</li>
    <li>Quality Concrete Workmanship</li>
    <li>Modern Equipment &amp; Technology</li>
    <li>Commitment to Client Satisfaction</li>
  </ul>

  <h2 class="section-heading" style="left:32px; top:1003px;">LET'S BUILD YOUR NEXT<br>PROJECT</h2>
  <div class="rule" style="left:32px; top:1066px;"></div>
  <p class="body-text" style="left:31px; top:1085px; width:394px;">Whether you're starting a new development, strengthening existing infrastructure, or need specialized geotechnical expertise, Keystone Ridge Construction is ready to help.</p>

  <div class="services-frame"></div>
  <div class="services-card"></div>
  <h2 class="section-heading" style="left:407px; top:603px;">OUR SERVICES</h2>
  <div class="rule" style="left:408px; top:636px;"></div>

  <div class="service" style="top:660px;">
    <svg class="service-icon" viewBox="0 0 48 48" aria-hidden="true">
      <circle cx="24" cy="24" r="24" fill="var(--navy)"/>
      <g fill="none" stroke="#fff" stroke-width="1.3">
        <rect x="11" y="17" width="26" height="18"/>
        <path d="M24 11v26M21 15l6 3M21 20l6 3M21 25l6 3M21 30l6 3"/>
      </g>
    </svg>
    <h3 class="service-title">GEOTECHNICAL SERVICES</h3>
    <p class="service-text">Reliable geotechnical solutions for safe, stable construction.</p>
  </div>

  <div class="service" style="top:743px;">
    <svg class="service-icon" viewBox="0 0 48 48" aria-hidden="true">
      <circle cx="24" cy="24" r="24" fill="var(--navy)"/>
      <g fill="none" stroke="#fff" stroke-width="1.3">
        <path d="M10 15h28M10 20h28M10 28h28M10 33h28"/>
        <path d="M12 26l2-4M16 26l2-4M20 26l2-4M24 26l2-4M28 26l2-4M32 26l2-4"/>
      </g>
    </svg>
    <h3 class="service-title">CONCRETE CONSTRUCTION</h3>
    <p class="service-text">Quality concrete solutions built for strength and durability.</p>
  </div>

  <div class="service" style="top:827px;">
    <svg class="service-icon" viewBox="0 0 48 48" aria-hidden="true">
      <circle cx="24" cy="24" r="24" fill="var(--navy)"/>
      <g fill="none" stroke="#fff" stroke-width="1.5">
        <path d="M24 10l11 4v9c0 7-5 12-11 15-6-3-11-8-11-15v-9z"/>
        <circle cx="24" cy="24" r="6"/>
        <path d="M21 24l2 2 4-4"/>
      </g>
    </svg>
    <h3 class="service-title">SOIL STABILIZATION</h3>
    <p class="service-text">Improving weak soils to create stable building platforms.</p>
  </div>

  <div class="service" style="top:910px;">
    <svg class="service-icon" viewBox="0 0 48 48" aria-hidden="true">
      <circle cx="24" cy="24" r="24" fill="var(--navy)"/>
      <g fill="none" stroke="#fff" stroke-width="1.5">
        <circle cx="24" cy="24" r="6"/>
        <path d="M24 12v4M24 32v4M12 24h4M32 24h4M15.5 15.5l2.8 2.8M29.7 29.7l2.8 2.8M15.5 32.5l2.8-2.8M29.7 18.3l2.8-2.8"/>
      </g>
    </svg>
    <h3 class="service-title">FOUNDATION CONSTRUCTION</h3>
    <p class="service-text">Building strong, dependable foundations for every project.</p>
  </div>

  <p class="call-label">Call Now!</p>
  <p class="call-number">+ 1 888 888 8888</p>
  <div class="contact-line"></div>
  <dl class="contact-list">
    <dt>Email</dt><dd>info@keystoneridgeconstruction.com</dd>
    <dt>Website</dt><dd>www.keystoneridgeconstruction.com</dd>
    <dt>Office Address</dt><dd>1234 Construction Way Suite 200 City, State ZIP</dd>
  </dl>

</main>
</body>
</html>
```